RWT Fittings Ltd Business Cards

We need a business card with our business logo. We provide window and door installations on high-rises in west coast British Colombia, Canada.

I would like my business information and details on one side of the card, and the other side the company name with logo

Target Market(s)

General Contractors

Industry/Entity Type

Construction

Contact Information for Business Card

one side i want my company name and logo in the dark theme logo that i provided

Requirements
Must have
• Marco Peltieri, 16045518293, RWTFittings@mailbox-demo.com, 1407-5194 Linden Row Burnaby BC, V5H 2K9, Owner & Manager

```html
<!DOCTYPE html>
<html lang="en">
<head>
<meta charset="utf-8">
<title>RWT Fittings Ltd Business Cards</title>
<link rel="stylesheet" href="https://fonts.googleapis.com/css2?family=Oswald:wght@600&family=Poppins:wght@400;600&display=swap">
<style>
  :root {
    --backdrop: #161616;
    --card: #262626;
    --card-edge: #303030;
    --accent: #1ea5e0;
    --text: #ededed;
    --mark: #8c8c8c;
  }
  * { margin: 0; padding: 0; box-sizing: border-box; }
  html, body { width: 1200px; height: 900px; overflow: hidden; }
  body {
    background: var(--backdrop);
    font-family: "Poppins", sans-serif;
    color: var(--text);
    position: relative;
  }
  .card {
    position: absolute;
    left: 280px;
    width: 640px;
    height: 366px;
    background: linear-gradient(135deg, var(--card) 0%, var(--card-edge) 100%);
  }
  .card--front { top: 60px; }
  .card--back { top: 470px; }

  .brand {
    position: absolute;
    inset: 0;
    display: flex;
    align-items: center;
    justify-content: center;
    gap: 18px;
  }
  .brand__square {
    width: 54px;
    height: 54px;
    background: var(--mark);
  }
  .brand__name {
    font-family: "Poppins", sans-serif;
    font-weight: 600;
    font-size: 44px;
    letter-spacing: 2px;
    color: var(--mark);
  }

  .details {
    position: absolute;
    left: 0;
    right: 0;
    top: 116px;
    display: flex;
    justify-content: center;
    align-items: stretch;
    gap: 14px;
  }
  .person { text-align: right; }
  .person__name {
    font-family: "Oswald", sans-serif;
    font-weight: 600;
    font-size: 38px;
    line-height: 1;
    color: var(--accent);
    text-transform: uppercase;
    font-style: italic;
    white-space: nowrap;
  }
  .person__title {
    font-size: 15px;
    margin-top: 6px;
    letter-spacing: 0.5px;
    white-space: nowrap;
  }
  .divider {
    width: 3px;
    background: var(--accent);
  }
  .contacts {
    list-style: none;
    font-size: 15px;
    line-height: 22px;
  }
  .contacts li { display: flex; align-items: center; gap: 7px; white-space: nowrap; }
  .contacts svg { width: 14px; height: 14px; flex: none; }
  .contacts .hl { color: var(--accent); }
  .address {
    position: absolute;
    left: 140px;
    top: 250px;
    font-size: 17px;
    letter-spacing: 0.3px;
    white-space: nowrap;
  }
</style>
</head>
<body>
  <section class="card card--front" aria-label="Card front">
    <div class="brand">
      <span class="brand__square"></span>
      <span class="brand__name">RWT FITTINGS LTD</span>
    </div>
  </section>

  <section class="card card--back" aria-label="Card back">
    <div class="details">
      <div class="person">
        <div class="person__name">Marco Peltieri</div>
        <div class="person__title">Owner &amp; Manager</div>
      </div>
      <span class="divider"></span>
      <ul class="contacts">
        <li>
          <svg viewBox="0 0 16 16" fill="none" stroke="#1ea5e0" stroke-width="1.6"><path d="M4 1.5 6 5 4.6 6.5c.8 2 2.3 3.6 4.3 4.5L10.5 9.5 14 11.5 12.8 14C7 13.6 2.4 9 2 3.2z"/></svg>
          1-604-551-8293
        </li>
        <li>
          <svg viewBox="0 0 16 16" fill="none" stroke="#1ea5e0" stroke-width="1.5"><rect x="1.5" y="3.5" width="13" height="9"/><path d="M1.5 3.5 8 9l6.5-5.5"/></svg>
          RWTFittings@mailbox-demo.com
        </li>
        <li>
          <svg viewBox="0 0 16 16" fill="none" stroke="#1ea5e0" stroke-width="1.4"><circle cx="8" cy="8" r="6.5"/><ellipse cx="8" cy="8" rx="3" ry="6.5"/><path d="M1.5 8h13M2.5 5h11M2.5 11h11"/></svg>
          <span>www.<span class="hl">rwtfittingsltd</span>.com</span>
        </li>
      </ul>
    </div>
    <p class="address">1407-5194 Linden Row Burnaby BC, V5H 2K9</p>
  </section>
</body>
</html>
```